Marlow Ridge Rehab and Wellness Postcard

This is a postcard for our chiropractic office, to raise awareness of our practice. Please refer to our grand opening flyer for contact information and logo. Please include the following:
Marlow Ridge Rehab and Wellness
Chiropractic & Wellness
Spinal Correction
Injury Rehabilitation
Tired of living with Fatigue, Allergies, High/Low Blood Pressure, Headaches, Numbness/Tingling in Hands/Feet, Frequent Infection, Back Pain, Neck Pain or ANY Other Health Problems?
Call Today for a Free Consultation with the Doctor!
(Space is Limited, Please Call to Reserve)

```html
<!DOCTYPE html>
<html lang="en">
<head>
<meta charset="utf-8">
<title>Marlow Ridge Rehab and Wellness Postcard</title>
<link href="https://fonts.googleapis.com/css2?family=Open+Sans:wght@300;400;600;700;800&display=swap" rel="stylesheet">
<style>
  :root {
    --page: #eef2f4;
    --blue: #1b75bc;
    --navy: #0f3355;
    --cyan: #1fb3e8;
    --white: #ffffff;
    --logo-blue: #2b6fae;
    --line: #555555;
  }
  * { box-sizing: border-box; margin: 0; padding: 0; }
  html, body { width: 1200px; height: 891px; overflow: hidden; }
  body { background: var(--page); font-family: "Open Sans", sans-serif; position: relative; }
  .card {
    position: absolute; top: 257px; width: 565px; height: 377px;
    background: var(--white); overflow: hidden;
    box-shadow: 0 6px 18px rgba(0,0,0,0.15);
  }
  .card--front { left: 25px; }
  .card--back { left: 610px; }
  .card svg.shapes { position: absolute; inset: 0; }
  .abs { position: absolute; color: var(--white); }

  /* front */
  .spine-art {
    position: absolute; left: 230px; top: 0; width: 335px; height: 377px;
    background:
      linear-gradient(100deg, rgba(255,255,255,0) 25%, rgba(240,150,70,0.28) 45%, rgba(255,255,255,0) 62%),
      radial-gradient(ellipse at 55% 50%, #ffffff 0%, #d8d8d8 55%, #9c9c9c 100%);
  }
  .services { left: 34px; top: 24px; font-weight: 800; font-size: 15.5px; line-height: 1.35; letter-spacing: 0.2px; }
  .services li { list-style: none; margin-bottom: 7px; }
  .symptoms { left: 30px; top: 137px; width: 245px; font-size: 10.6px; line-height: 1.5; }
  .symptoms strong { font-weight: 700; }
  .call { left: 28px; top: 245px; }
  .call__lead { font-weight: 800; font-size: 21px; line-height: 1.1; }
  .call__offer { font-weight: 700; font-size: 17px; line-height: 1.15; }
  .call__doctor { font-weight: 700; font-size: 10.5px; }
  .call__phone { display: flex; align-items: center; gap: 6px; font-weight: 800; font-size: 25px; margin-top: 4px; }
  .call__note { font-size: 9.5px; margin-top: 3px; }

  .brand { position: absolute; display: flex; align-items: center; gap: 6px; color: var(--logo-blue); font-weight: 600; line-height: 1.2; }
  .brand__dot { flex: none; border-radius: 50%; background: var(--logo-blue); }
  .brand--front { left: 440px; top: 40px; font-size: 14px; }
  .brand--front .brand__dot { width: 14px; height: 14px; }
  .brand--back { left: 368px; top: 30px; font-size: 11px; }
  .brand--back .brand__dot { width: 11px; height: 11px; }

  /* back */
  .photo-area {
    position: absolute; left: 0; top: 0; width: 330px; height: 150px;
    background: linear-gradient(120deg, #e7f1f8 0%, #c9dceb 55%, #aac7de 100%);
  }
  .office { left: 20px; top: 160px; font-size: 9.5px; line-height: 1.45; }
  .office__title { font-size: 15px; font-weight: 300; margin-bottom: 6px; }
  .office__title b { font-weight: 800; }
  .office__row { display: flex; gap: 6px; align-items: flex-start; }
  .office__web { left: 160px; top: 300px; font-size: 9.5px; }
  .serving { left: 20px; top: 336px; width: 270px; font-size: 8.5px; line-height: 1.4; }
  .serving b { font-weight: 800; }
  .stamp { position: absolute; left: 475px; top: 28px; width: 70px; height: 46px; border: 1px solid var(--line); }
  .address-line { position: absolute; left: 395px; width: 150px; height: 1px; background: var(--line); }
  .address-line--1 { top: 160px; }
  .address-line--2 { top: 185px; }
  .address-line--3 { top: 210px; }
</style>
</head>
<body>

<section class="card card--front">
  <div class="spine-art" role="img" aria-label="Illustration of a human spine with glowing orange discs"></div>
  <svg class="shapes" width="565" height="377" viewBox="0 0 565 377">
    <polygon points="0,0 226,0 322,246 262,377 0,377" fill="var(--cyan)"/>
    <polygon points="0,0 215,0 306,246 250,377 0,377" fill="var(--blue)"/>
    <polygon points="0,122 264,122 296,226 0,226" fill="var(--navy)"/>
  </svg>
  <ul class="abs services">
    <li>CHIROPRACTIC &amp;<br>WELLNESS</li>
    <li>SPINAL CORRECTION</li>
    <li>INJURY REHABILITATION</li>
  </ul>
  <p class="abs symptoms">Tired of living with Fatigue, Allergies, High/Low Blood Pressure, Headaches, Numbness/Tingling in Hands/Feet, Frequent Infection, Back Pain, Neck Pain or ANY Other <strong>Health Problems?</strong></p>
  <div class="abs call">
    <p class="call__lead">CALL TODAY</p>
    <p class="call__offer">for a Free Consultation</p>
    <p class="call__doctor">with the Doctor!</p>
    <p class="call__phone">
      <svg width="18" height="18" viewBox="0 0 24 24" aria-hidden="true"><circle cx="12" cy="12" r="10.5" fill="none" stroke="#fff" stroke-width="1.8"/><path d="M9 6.5c-1 .3-2 1.4-1.6 3 .8 3.3 3.6 6.6 6.6 7.7 1.5.5 2.6-.3 3-1.3l-2-1.8-1.4.9c-1.4-.7-2.7-2.2-3.2-3.6l1-1.2z" fill="#fff"/></svg>
      555-014-3200
    </p>
    <p class="call__note">(Space is Limited, Please Call to Reserve)</p>
  </div>
  <div class="brand brand--front"><span class="brand__dot"></span><span>Marlow Ridge<br>Rehab</span></div>
</section>

<section class="card card--back">
  <div class="photo-area" role="img" aria-label="Photo of a smiling doctor with an older patient in a bright clinic"></div>
  <svg class="shapes" width="565" height="377" viewBox="0 0 565 377">
    <polygon points="330,0 340,0 376,215 316,377 306,377 366,215" fill="var(--cyan)"/>
    <polygon points="0,150 358,150 366,215 314,330 0,330" fill="var(--blue)"/>
    <polygon points="0,330 314,330 294,377 0,377" fill="var(--navy)"/>
  </svg>
  <div class="abs office">
    <p class="office__title">Our <b>office</b></p>
    <div class="office__row">
      <svg width="9" height="11" viewBox="0 0 12 16" aria-hidden="true"><path d="M6 0a6 6 0 0 0-6 6c0 4.5 6 10 6 10s6-5.5 6-10a6 6 0 0 0-6-6zm0 8.5A2.5 2.5 0 1 1 6 3.5a2.5 2.5 0 0 1 0 5z" fill="#fff"/></svg>
      <p>Marlow Ridge Rehab and Wellness<br>48 Alder Lane, Suite 120<br>Marlow Ridge, NJ 07010</p>
    </div>
    <p class="office__row">✉ info@marlowridgerehab.com</p>
    <p class="office__row"><b>✆ 555-014-3200</b></p>
  </div>
  <p class="abs office__web">www.marlowridgerehab.com</p>
  <p class="abs serving"><b>Proudly Serving:</b> Marlow Ridge, Fenwick, Ashby, Corland and the greater Hollis County</p>
  <div class="brand brand--back"><span class="brand__dot"></span><span>Marlow Ridge<br>Rehab</span></div>
  <div class="stamp"></div>
  <div class="address-line address-line--1"></div>
  <div class="address-line address-line--2"></div>
  <div class="address-line address-line--3"></div>
</section>

</body>
</html>
```